New Organic Medical Marijuana Packging Design

New Organic Grower needs a fresh new design for the retail package.
the idea is to incorporate a compostable materials and come up with the resealable pouch/baggy that can hold the medicine and maybe another compartment for the promotional material (like rolling papers).
Company name is Gerry's Organic. (gerry- Gerald is the name of our guru grower who also spends a ton of time playing in the dirt).
Medicine will need to be visible (whole or partially )through the side of the pack. an idea attached..

```html
<!DOCTYPE html>
<html lang="en">
<head>
<meta charset="utf-8">
<title>Gerry's Organic – Medicinal Marijuana Pouch</title>
<link rel="stylesheet" href="https://fonts.googleapis.com/css2?family=Teko:wght@600&family=Open+Sans:wght@400&display=swap">
<style>
  :root {
    --backdrop: #dde7ee;
    --pouch: #3b3b3c;
    --pouch-seam: #333334;
    --leaf-deep: #0b6a1e;
    --leaf-mid: #1fa23a;
    --leaf-light: #e9f7ec;
    --brand-green: #29b34a;
    --ink-white: #ffffff;
  }
  * { margin: 0; padding: 0; box-sizing: border-box; }
  html, body {
    width: 1200px;
    height: 840px;
    overflow: hidden;
    background: var(--backdrop);
  }
  .canvas {
    position: relative;
    width: 1200px;
    height: 840px;
  }
  .pouch-face {
    position: absolute;
    left: 365px;
    top: 68px;
    width: 470px;
    height: 730px;
    background: var(--pouch);
    overflow: hidden;
  }
  .zip-seam {
    position: absolute;
    left: 0;
    right: 0;
    top: 108px;
    height: 3px;
    background: var(--pouch-seam);
  }
  .leaf-art {
    position: absolute;
    left: 95px;
    top: 132px;
    width: 320px;
    height: 330px;
    border-radius: 46% 46% 40% 40%;
    background: radial-gradient(circle at 62% 58%, var(--leaf-light) 0%, var(--leaf-mid) 38%, var(--leaf-deep) 80%);
  }
  .brand-name {
    position: absolute;
    left: 0;
    right: 0;
    top: 482px;
    text-align: center;
    font-family: "Teko", "Arial Narrow", sans-serif;
    font-weight: 600;
    font-size: 84px;
    line-height: 66px;
    letter-spacing: 3px;
    color: var(--ink-white);
    text-transform: uppercase;
  }
  .product-band {
    position: absolute;
    left: 0;
    right: 0;
    top: 644px;
    height: 62px;
    background: var(--brand-green);
    display: flex;
    align-items: center;
    justify-content: center;
  }
  .product-type {
    font-family: "Open Sans", Arial, sans-serif;
    font-size: 21px;
    letter-spacing: 0.5px;
    color: var(--ink-white);
  }
</style>
</head>
<body>
  <main class="canvas">
    <section class="pouch-face">
      <div class="zip-seam"></div>
      <div class="leaf-art" role="img" aria-label="Large green cannabis leaf illustration"></div>
      <h1 class="brand-name">Gerry's<br>Organic</h1>
      <div class="product-band">
        <p class="product-type">medicinal marijuana</p>
      </div>
    </section>
  </main>
</body>
</html>
```